Luxury Wine Label for New Startup Winery

We need a wine label for our new winery startup. We have worked with a local designer but do not feel the resulting label / logo have the elevation required to present our brand as a luxury wine. Our winery is called "Quailbrook Vineyards" and we are focused on extremely high quality hand crafted artisan and estate wines from the Pacific Northwest.
We would like to see designs that utilize a tree line, or other imagery that represents the "Quailbrook" part of our company name. Another interesting feature could be wood grain.
A logo will be required based on your design so please design with this in mind:
This logo should be consistent with the wine bottle label design, and should be representative of our high end exclusive wine while giving a sense of place (Oregon/ Pacific Northwest.)
I will supply an image of the design we received from our local designer, PLEASE NOTE: in general we do like wood grain and tree line concepts but feel the execution was poorly done.
ATTN: Logo design should be suitable for use on: Bottles (Red wine/rose/white wine), Bussiness cards, vehicle signage, business signage, etc
P.S.:
If you have a design that is not outside the box we are still interested in seeing it.
Label is for a burgundy style bottle with a label height of 3.5 - 4" and a width of 3.5-4"
any label <= 4"x4" and >=3.5"x3.5" will be acceptable:
HOWEVER Width should be greater than or equal to height due to the bottle format
Target Market(s)
Wine enthusiasts with adequate discretionary budgets to afford $100 bottles of wine.
Industry/Entity Type
Wine / Winery
Requirements
Must have
- A sense of luxury, a feel of exclusivity, and a theme consistent with our product and brand name
Nice to have
- Tree line, wood grain or other wood themes. Serif fonts
Should not have
- anything cheesy, off topic, hard to read script fonts or anything that makes the label hard to read from a few feet away or too busy

```html
<!DOCTYPE html>
<html lang="en">
<head>
<meta charset="UTF-8">
<title>Quailbrook Vineyards – Wine Label</title>
<link href="https://fonts.googleapis.com/css2?family=Cinzel:wght@400&family=Pinyon+Script&family=Montserrat:wght@400;600&display=swap" rel="stylesheet">
<style>
  :root {
    --backdrop: #232625;
    --label-paper: #eceee7;
    --ink: #3b3e3d;
    --ink-soft: #5b5f5d;
    --tree-dark: #7d827f;
    --tree-light: #b9bdb8;
  }
  html, body {
    margin: 0;
    padding: 0;
    width: 1200px;
    height: 1200px;
    overflow: hidden;
    background: var(--backdrop);
  }
  .canvas {
    position: relative;
    width: 1200px;
    height: 1200px;
  }
  .label {
    position: absolute;
    left: 100px;
    top: 150px;
    width: 1000px;
    height: 900px;
    box-sizing: border-box;
    padding-top: 60px;
    background: var(--label-paper);
    color: var(--ink);
    text-align: center;
    display: flex;
    flex-direction: column;
    align-items: center;
  }
  .tree-emblem {
    width: 160px;
    height: 250px;
    border-radius: 4px;
    background: radial-gradient(ellipse at 50% 40%, var(--tree-dark), var(--tree-light) 75%, var(--label-paper));
  }
  .brand-name {
    margin: 50px 0 0;
    font-family: "Cinzel", serif;
    font-weight: 400;
    font-size: 116px;
    letter-spacing: 2px;
    line-height: 1;
  }
  .brand-sub {
    margin: 28px 0 0;
    font-family: "Cinzel", serif;
    font-size: 50px;
    letter-spacing: 14px;
    line-height: 1;
    color: var(--ink-soft);
  }
  .region {
    margin: 62px 0 0;
    font-family: "Pinyon Script", cursive;
    font-size: 64px;
    line-height: 1;
    color: var(--ink-soft);
  }
  .estate-line {
    margin: 26px 0 0;
    font-family: "Montserrat", sans-serif;
    font-weight: 600;
    font-size: 40px;
    letter-spacing: 4px;
    line-height: 1;
  }
  .alcohol {
    position: absolute;
    right: 28px;
    bottom: 26px;
    margin: 0;
    font-family: "Montserrat", sans-serif;
    font-weight: 400;
    font-size: 20px;
    color: var(--ink-soft);
  }
</style>
</head>
<body>
  <main class="canvas">
    <section class="label">
      <div class="tree-emblem" role="img" aria-label="Illustration of two evergreen trees"></div>
      <h1 class="brand-name">QUAILBROOK</h1>
      <p class="brand-sub">VINEYARDS</p>
      <p class="region">Pacific Northwest</p>
      <p class="estate-line">ESTATE WINE</p>
      <p class="alcohol">13%</p>
    </section>
  </main>
</body>
</html>
```